Stylish Business Cards Wanted

- DOUBLE SIDED Design Required -

High end, edgy cards for a corporate and personal stylist. Must include logo,
Name: Belinda Harwick
Title: Director and Stylist
telephone : +61 8 7142 5809
email: belinda@theloombriefing.example
website: theloombriefing.example
Tag: Corporate Workwear & Uniform Specialist | Personal Stylist
Would like nice icons for telephone, email, website

Target Market(s)

Businesses wanting stylish uniforms, people wanting stylish wardrobes

Industry/Entity Type

Corporate Workwear Stylist

Contact Information for Business Card

I would like black, white and gold foiling incorporated in the design - possibly a touch of the other colours on my branding guide attached Name: Belinda Harwick Title: Director and Stylist telephone : +61 8 7142 5809 email: belinda@theloombriefing.example website: theloombriefing.example Tag: Corporate Workwear & Uniform Specialist | Personal Stylist Would like nice icons for telephone, email, website

Font styles to use
Other font styles liked:
• Raleway

Colors

Designer to choose colors to be used in the design.

Requirements
Must have
• Gold foil accents

```html
<!DOCTYPE html>
<html lang="en">
<head>
<meta charset="utf-8">
<title>The Loom Briefing – Business Cards</title>
<link rel="stylesheet" href="https://fonts.googleapis.com/css2?family=Montserrat:wght@400;500;700&display=swap">
<style>
  :root {
    --backdrop: #2b2b2b;
    --card: #232323;
    --gold: #e8b94a;
    --white: #ffffff;
    --text-font: "Montserrat", sans-serif;
  }
  * { margin: 0; padding: 0; box-sizing: border-box; }
  html, body {
    width: 1200px; height: 900px; overflow: hidden;
    background: var(--backdrop);
    font-family: var(--text-font);
  }
  .canvas { position: relative; width: 1200px; height: 900px; }

  .card {
    position: absolute;
    left: 250px;
    width: 700px;
    height: 400px;
    background: var(--card);
    border-left: 4px solid var(--gold);
    border-bottom: 4px solid var(--gold);
    box-shadow: 0 14px 30px rgba(0,0,0,0.45);
  }
  .card--front { top: 30px; }
  .card--back { top: 470px; }

  /* wordmark */
  .wordmark {
    position: absolute;
    display: flex;
    align-items: center;
    gap: 12px;
  }
  .wordmark__square {
    width: 16px; height: 16px;
    background: var(--gold);
  }
  .wordmark__name {
    color: var(--white);
    font-weight: 500;
    letter-spacing: 0.04em;
    white-space: nowrap;
  }
  .card--front .wordmark { left: 200px; top: 140px; }
  .card--front .wordmark__name { font-size: 34px; }
  .card--back .wordmark { right: 50px; top: 205px; }
  .card--back .wordmark__name { font-size: 28px; }

  .tagline {
    position: absolute;
    left: 0; right: 0; bottom: 40px;
    text-align: center;
    color: var(--gold);
    font-size: 16px;
    font-weight: 500;
    letter-spacing: 0.02em;
  }

  /* back side */
  .name-tab {
    position: absolute;
    left: -4px; top: 52px;
    width: 18px; height: 44px;
    background: var(--gold);
  }
  .identity { position: absolute; left: 36px; top: 50px; }
  .identity__name {
    color: var(--gold);
    font-size: 26px;
    font-weight: 700;
    letter-spacing: 0.06em;
    text-transform: uppercase;
  }
  .identity__title {
    color: var(--white);
    font-size: 16px;
    font-weight: 400;
    letter-spacing: 0.03em;
    margin-top: 2px;
  }
  .contacts {
    position: absolute;
    left: 36px; bottom: 50px;
    list-style: none;
  }
  .contacts__item {
    display: flex;
    align-items: center;
    gap: 12px;
    color: var(--white);
    font-size: 18px;
    letter-spacing: 0.02em;
    line-height: 34px;
  }
  .contacts__icon { width: 18px; height: 18px; flex: none; }
</style>
</head>
<body>
<main class="canvas">

  <section class="card card--front" aria-label="Business card front">
    <div class="wordmark">
      <span class="wordmark__square"></span>
      <span class="wordmark__name">THE LOOM BRIEFING</span>
    </div>
    <p class="tagline">Corporate Workwear &amp; Uniform Specialist | Personal Stylist</p>
  </section>

  <section class="card card--back" aria-label="Business card back">
    <span class="name-tab"></span>
    <div class="identity">
      <h1 class="identity__name">Belinda Harwick</h1>
      <p class="identity__title">Director and Stylist</p>
    </div>

    <ul class="contacts">
      <li class="contacts__item">
        <svg class="contacts__icon" viewBox="0 0 24 24" aria-hidden="true">
          <path fill="#e8b94a" d="M6.6 10.8a15.1 15.1 0 0 0 6.6 6.6l2.2-2.2a1 1 0 0 1 1-.25 11.4 11.4 0 0 0 3.6.57 1 1 0 0 1 1 1V20a1 1 0 0 1-1 1A17 17 0 0 1 3 4a1 1 0 0 1 1-1h3.5a1 1 0 0 1 1 1c0 1.25.2 2.45.57 3.57a1 1 0 0 1-.25 1z"/>
        </svg>
        +61 8 7142 5809
      </li>
      <li class="contacts__item">
        <svg class="contacts__icon" viewBox="0 0 24 24" aria-hidden="true">
          <rect x="2" y="5" width="20" height="14" fill="#e8b94a"/>
          <path d="M2 5l10 8 10-8" fill="none" stroke="#232323" stroke-width="1.8"/>
        </svg>
        belinda@theloombriefing.example
      </li>
      <li class="contacts__item">
        <svg class="contacts__icon" viewBox="0 0 24 24" aria-hidden="true">
          <circle cx="12" cy="12" r="10" fill="#e8b94a"/>
          <path d="M2 12h20M12 2c3 3 3 17 0 20M12 2c-3 3-3 17 0 20" fill="none" stroke="#232323" stroke-width="1.5"/>
        </svg>
        www.theloombriefing.example
      </li>
    </ul>

    <div class="wordmark">
      <span class="wordmark__square"></span>
      <span class="wordmark__name">THE LOOM BRIEFING</span>
    </div>
  </section>

</main>
</body>
</html>
```